Redesign of outdated "Automotive Automation Company"

We are looking to finally update our outdated website with some cutting edge graphics. We want our customers to know we value technology and are cutting edge as far as design. We provide automation solutions for the automotive industry which essentially means we program robots, and sell automation related products.

Current URL

http://lnk.qorvi.example/Tm4pzr
Updates

Project Deadline Extended
Reason: The client portal wasn't working, it's just finally been fixed by Pixel Harbor. I will go through and start reviewing designs.

We are trying to go with the same look and feel on our business cards, line cards, apparel, etc. so we are forming a brand. I have included the current draft of the line card. Please utilize our newest Logo VEL Standardized Logo.jpg http://img.plomtra.example/zuKe9rb.jpg?1 Also we are trying hard to sell the following software / hardware companies so we can put some emphasis on their product. Corvane Systems https://www.corvanesystems.example/ We make money on selling the software and then on the integration. I think you should tie in this animation. ยท Shop Line Muddle to Momentum https://media.vuntelo.example/clips/9b2e7f1d04c3a85e6f2d1b7c9a0e4f3d8c6b2a1e.jpg?image_play_button=true&image_play_button_color=7b796ae0&image_crop_resized=275x155 In this 2-minute video, discover how Trellan can help run your plant floor. We are Authorized Integrators / Resellers for Pembry Controls Hadrix Sensorik http://hadrix.example/en/usa/ Corvane Systems https://www.corvanesystems.example/ Unified Motion Works www.umwkq.example Brisk Beltway Corp www.briskbeltway.example Castmere Fabrication http://www.castmerefab.example/strategic_partners.aspx

Target Market(s)

Large automotive companies looking for automation or robotic programming. So Professional is key.

Industry/Entity Type

Automotive

Font styles to use
Other font styles liked:
• Possible Open Sans or Lato

Colors
0591cc
ceeaf6
fbd4d5
fbf289
fece3e

Requirements
Must have
• Professional Modern Design.

I want a homepage design, and a rough Sales Page... Where numerous products can be listed.
Nice to have
• Maybe an updated logo if possible.

```html
<!DOCTYPE html>
<html lang="en">
<head>
<meta charset="utf-8">
<title>VEL Engineering Solutions</title>
<link href="https://fonts.googleapis.com/css2?family=Open+Sans:ital,wght@0,400;0,600;0,700;1,400&display=swap" rel="stylesheet">
<style>
:root{
  --red:#d7201f;
  --red-dark:#b81717;
  --ink:#2b2b2b;
  --text:#6f6f6f;
  --muted:#8a8a8a;
  --pale:#f6f6f6;
  --band:#eeeeee;
  --footer:#2e2e2e;
  --footer-base:#222222;
  --footer-text:#9a9a9a;
  --white:#ffffff;
}
*{margin:0;padding:0;box-sizing:border-box}
html,body{width:1200px;height:2507px;overflow:hidden}
body{font-family:"Open Sans",Arial,sans-serif;color:var(--text);background:var(--white);position:relative}

/* header */
.site-header{position:absolute;left:0;top:0;width:1200px;height:120px;background:var(--white)}
.brand{position:absolute;left:100px;top:22px;display:flex;align-items:center;gap:12px}
.brand-mark{width:60px;height:60px;border-radius:50%;background:var(--red)}
.brand-name{font-size:22px;font-weight:700;color:var(--ink);line-height:1.1}
.brand-name small{display:block;font-size:10px;font-weight:600;color:var(--muted);letter-spacing:1px}
.phone{position:absolute;left:805px;top:24px;font-size:17px;color:var(--red);font-weight:600}
.btn-contact{position:absolute;left:958px;top:17px;width:145px;height:38px;background:var(--red);color:var(--white);font-size:12px;font-weight:700;display:flex;align-items:center;justify-content:center;border-radius:2px}
.main-nav{position:absolute;top:79px;left:0;width:1200px;font-size:12px;font-weight:700;color:#555}
.main-nav span{position:absolute}

/* hero */
.hero{position:absolute;left:0;top:120px;width:1200px;height:478px;
  background:
    radial-gradient(ellipse 300px 330px at 230px 260px,rgba(250,246,242,0.95),rgba(250,246,242,0) 70%),
    radial-gradient(ellipse 120px 90px at 330px 470px,rgba(255,255,255,0.9),rgba(255,255,255,0) 70%),
    radial-gradient(ellipse 340px 140px at 850px 330px,rgba(92,76,66,0.42),rgba(92,76,66,0) 72%),
    linear-gradient(180deg,rgba(0,0,0,0) 86%,rgba(255,255,255,0.45) 90%,rgba(235,235,233,0.6) 100%),
    radial-gradient(ellipse 900px 420px at 640px 180px,#e4e4e1,#c6c6c3 80%),
    #c9c9c6}
.hero-title{position:absolute;left:473px;top:56px;font-size:35.5px;font-weight:400;color:#333;letter-spacing:0.5px}
.hero-sub{position:absolute;left:473px;top:104px;font-size:28.5px;font-weight:700;color:var(--red)}

/* distributors */
.partners{position:absolute;left:0;top:598px;width:1200px;height:82px;background:var(--band)}
.partners-label{position:absolute;left:0;top:0;width:381px;height:82px;background:var(--red);color:var(--white);font-size:18px;display:flex;align-items:center;justify-content:center}
.partner{position:absolute;top:0;height:82px;display:flex;align-items:center;gap:9px;font-size:20px;font-weight:700;color:#333}
.partner i{width:17px;height:17px;background:var(--red);display:block}

/* welcome */
.welcome{position:absolute;left:0;top:680px;width:1200px;height:217px;background:var(--pale);text-align:center}
.section-title{font-size:20px;font-weight:700;color:var(--ink);text-align:center;letter-spacing:0.3px}
.welcome .section-title{position:absolute;top:57px;width:100%}
.welcome p{position:absolute;left:155px;top:97px;width:890px;font-size:11.2px;line-height:25px;color:var(--muted)}

/* services */
.services{position:absolute;left:0;top:897px;width:1200px;height:794px;background:linear-gradient(#fff 0%,#fff 68%,#f1f1f1 100%)}
.services .section-title{position:absolute;top:45px;width:100%}
.intro{position:absolute;left:0;width:1200px;text-align:center;font-size:13.8px;line-height:26px;color:var(--muted)}
.service{position:absolute;width:325px}
.service svg{position:absolute;left:0;top:2px}
.service h3{margin-left:48px;font-size:15px;font-weight:400;color:var(--red)}
.service p{margin-left:48px;margin-top:6px;font-size:10.3px;line-height:20.5px;color:var(--muted)}
.divider{position:absolute;top:455px;height:1px;background:#e2e2e2}
.divider-knob{position:absolute;left:578px;top:435px;width:44px;height:44px;border:1px solid #e0e0e0;border-radius:50%;background:var(--white)}
.feature{position:absolute;top:528px;width:310px;height:189px}
.feature .photo{position:absolute;inset:0}
.feature .caption{position:absolute;left:0;bottom:0;width:100%;height:43px;background:var(--red);color:var(--white);font-size:14px;font-weight:600;display:flex;align-items:center;padding-left:18px}
.feature .caption svg{position:absolute;right:16px;top:15px}
.feature .shade{position:absolute;left:20px;top:205px;width:270px;height:14px;border-radius:50%;background:radial-gradient(rgba(0,0,0,0.16),rgba(0,0,0,0))}

/* team */
.team{position:absolute;left:0;top:1691px;width:1200px;height:501px;background:var(--white)}
.team .section-title{position:absolute;top:47px;width:100%}
.member{position:absolute;top:166px;width:231px;text-align:center}
.member .photo{width:231px;height:223px}
.member .quote{width:231px;height:223px;background:var(--red);color:var(--white);text-align:left;padding:38px 22px 0 40px;font-size:12.5px;line-height:23px;position:relative}
.member .quote b{position:absolute;font-size:26px;font-family:Georgia,serif;font-weight:400}
.member h4{margin-top:20px;font-size:12px;font-weight:700;color:var(--red)}
.member span{display:block;margin-top:4px;font-size:12.5px;color:#666}
.team-arrow{position:absolute;top:268px}

/* footer */
.site-footer{position:absolute;left:0;top:2192px;width:1200px;height:264px;background:var(--footer);color:var(--footer-text)}
.footer-col{position:absolute;top:40px}
.footer-col h5{font-size:12.5px;font-weight:700;color:var(--white);margin-bottom:14px}
.footer-col ul{list-style:none;font-size:10.5px;line-height:22.4px}
.testimonial{font-size:10.5px;line-height:21px;font-style:italic;color:#8d8d8d;width:300px;position:relative;padding-left:24px;padding-right:10px}
.testimonial b{position:absolute;font-family:Georgia,serif;font-style:normal;font-size:24px;color:#777;font-weight:400}
.testimonial-by{margin-top:22px;margin-left:20px;font-size:11.5px;color:#777}
.testimonial-by b{color:#cfcfcf}
.social li{display:flex;align-items:center;gap:8px;height:42px}
.social i{width:26px;height:26px;border-radius:50%;background:#5e5e5e;display:block}
.footer-base{position:absolute;left:0;top:2456px;width:1200px;height:51px;background:var(--footer-base);color:#7d7d7d;font-size:10.5px;display:flex;align-items:center;justify-content:center}
</style>
</head>
<body>

<header class="site-header">
  <div class="brand">
    <span class="brand-mark"></span>
    <div class="brand-name">VEL<small>AUTOMATION · ROBOTICS · CONTROLS</small></div>
  </div>
  <div class="phone">1-855-MOTION-7</div>
  <div class="btn-contact">CONTACT NOW</div>
  <nav class="main-nav">
    <span style="left:465px">HOME</span>
    <span style="left:563px">ABOUT US</span>
    <span style="left:686px">SERVICES</span>
    <span style="left:802px">CLIENTS</span>
    <span style="left:914px">SOLUTIONS</span>
    <span style="left:1045px">CONTACT</span>
  </nav>
</header>

<section class="hero" role="img" aria-label="Surprised young engineer in glasses beside a team of business people turning large gears on a concrete wall">
  <h1 class="hero-title">PROVIDING SOLUTIONS FOR</h1>
  <div class="hero-sub">AUTOMATION, ROBOTICS AND CONTROLS</div>
</section>

<section class="partners">
  <div class="partners-label">AUTHORIZED DISTRIBUTOR</div>
  <div class="partner" style="left:402px"><i></i>Hadrix Sensorik</div>
  <div class="partner" style="left:708px;font-weight:400;color:#555">Corvane Systems</div>
  <div class="partner" style="left:938px;color:var(--red)">Pembry Controls</div>
</section>

<section class="welcome">
  <h2 class="section-title">WELCOME TO VEL ENGINEERING SOLUTIONS</h2>
  <p>Industrial Automation is constantly evolving with ever-changing technological breakthroughs. For companies to remain competitive, they need to be more nimble than ever implementing productivity and manufacturing innovations. But identifying and implementing the right Automation, Robotics and Industrial Controls is never easy. That's where our team of experts comes in to play bringing our proven experience to the table.</p>
</section>

<section class="services">
  <h2 class="section-title">OUR SERVICES</h2>
  <div class="intro" style="top:86px">PROVIDING SOLUTIONS for Automation, Robotics and Controls by offering multiple disciplines that help you achieve your desired results.<br>Our TEAM delivers NEW solutions to maximize your projected outcome.</div>

  <div class="service" style="left:104px;top:178px">
    <svg width="28" height="28" viewBox="0 0 28 28"><circle cx="14" cy="14" r="13" fill="var(--red)"/><path d="M7 9c4 0 5 3 8 2s3 5 0 6-2 5-5 4" fill="none" stroke="#fff" stroke-width="2"/></svg>
    <h3>Applications engineering</h3>
    <p>Provide electrical and mechanical expertise to solve automation specific application problems by utilizing best known industry practices.</p>
  </div>
  <div class="service" style="left:448px;top:178px">
    <svg width="30" height="28" viewBox="0 0 30 28"><path d="M2 24A13 13 0 0 1 28 24Z" fill="var(--red)"/><circle cx="9" cy="16" r="2" fill="#fff"/><circle cx="15" cy="12" r="2" fill="#fff"/><circle cx="21" cy="16" r="2" fill="#fff"/></svg>
    <h3>Controls engineering</h3>
    <p>Provide electrical and mechanical expertise to solve automation specific application problems by utilizing best known industry practices.</p>
  </div>
  <div class="service" style="left:807px;top:178px">
    <svg width="32" height="30" viewBox="0 0 32 30"><circle cx="11" cy="17" r="8" fill="none" stroke="var(--red)" stroke-width="5" stroke-dasharray="3 2"/><circle cx="24" cy="8" r="5" fill="none" stroke="var(--red)" stroke-width="4" stroke-dasharray="2 2"/></svg>
    <h3>Design engineering</h3>
    <p>Provide electrical and mechanical expertise to solve automation specific application problems by utilizing best known industry practices.</p>
  </div>
  <div class="service" style="left:104px;top:313px">
    <svg width="32" height="28" viewBox="0 0 32 28"><rect x="1" y="2" width="30" height="19" rx="2" fill="var(--red)"/><rect x="4" y="5" width="24" height="13" fill="#fff"/><rect x="11" y="22" width="10" height="4" fill="var(--red)"/></svg>
    <h3>Design specification</h3>
    <p>Provide electrical and mechanical expertise to solve automation specific application problems by utilizing best known industry practices.</p>
  </div>
  <div class="service" style="left:448px;top:313px">
    <svg width="28" height="30" viewBox="0 0 28 30"><path d="M14 2a9 9 0 0 0-5 16v4h10v-4A9 9 0 0 0 14 2Z" fill="none" stroke="var(--red)" stroke-width="3"/><rect x="10" y="24" width="8" height="3" fill="var(--red)"/></svg>
    <h3>Electrical engineering</h3>
    <p>Provide electrical and mechanical expertise to solve automation specific application problems by utilizing best known industry practices.</p>
  </div>
  <div class="service" style="left:807px;top:313px">
    <svg width="32" height="32" viewBox="0 0 32 32"><path d="M3 29l8-8" stroke="var(--red)" stroke-width="4"/><rect x="11" y="8" width="12" height="14" rx="2" transform="rotate(45 17 15)" fill="var(--red)"/><path d="M19 7l5-5M25 13l5-5" stroke="var(--red)" stroke-width="3"/></svg>
    <h3>Field installation</h3>
    <p>Provide electrical and mechanical expertise to solve automation specific application problems by utilizing best known industry practices.</p>
  </div>

  <div class="divider" style="left:270px;width:295px"></div>
  <div class="divider" style="left:635px;width:295px"></div>
  <div class="divider-knob"><svg width="44" height="44" viewBox="0 0 44 44"><path d="M17 20l5 5 5-5" fill="none" stroke="#bbb" stroke-width="2"/></svg></div>

  <div class="feature" style="left:100px">
    <div class="photo" role="img" aria-label="Businessman leaping with a briefcase against a cloudy sky" style="background:radial-gradient(ellipse 90px 70px at 150px 80px,rgba(70,78,92,0.55),rgba(70,78,92,0) 70%),linear-gradient(180deg,#8c9db0 0%,#c3ccd6 45%,#e3e6e9 62%,#8d939a 80%,#5d6369 100%)"></div>
    <div class="caption">Get to know our Team approach<svg width="12" height="12" viewBox="0 0 12 12"><path d="M1 1l5 5-5 5M6 1l5 5-5 5" fill="none" stroke="#fff" stroke-width="1.6"/></svg></div>
    <div class="shade"></div>
  </div>
  <div class="feature" style="left:446px">
    <div class="photo" role="img" aria-label="Humanoid robot head in cool metallic tones" style="background:radial-gradient(ellipse 80px 110px at 165px 70px,#b9c4c4,rgba(120,140,140,0) 75%),radial-gradient(ellipse 140px 120px at 150px 140px,#2c3a3d,rgba(44,58,61,0) 80%),linear-gradient(135deg,#41585b,#7f9696)"></div>
    <div class="caption">This way to Automation success<svg width="12" height="12" viewBox="0 0 12 12"><path d="M1 1l5 5-5 5M6 1l5 5-5 5" fill="none" stroke="#fff" stroke-width="1.6"/></svg></div>
    <div class="shade"></div>
  </div>
  <div class="feature" style="left:794px">
    <div class="photo" role="img" aria-label="Smiling businesswoman holding up a light bulb on a black background" style="background:radial-gradient(ellipse 50px 55px at 60px 55px,rgba(235,225,205,0.85),rgba(235,225,205,0) 75%),radial-gradient(ellipse 110px 110px at 175px 95px,#7a5238,rgba(90,58,40,0) 75%),radial-gradient(ellipse 150px 60px at 190px 160px,#d8d8d8,rgba(216,216,216,0) 75%),#0d0d0d"></div>
    <div class="caption">Bring great ideas to your business<svg width="12" height="12" viewBox="0 0 12 12"><path d="M1 1l5 5-5 5M6 1l5 5-5 5" fill="none" stroke="#fff" stroke-width="1.6"/></svg></div>
    <div class="shade"></div>
  </div>
</section>

<section class="team">
  <h2 class="section-title">OUR SERVICES</h2>
  <div class="intro" style="top:86px">PROVIDING SOLUTIONS for Automation, Robotics and Controls by offering multiple disciplines that help you achieve your desired results.<br>Our TEAM delivers NEW solutions to maximize your projected outcome.</div>

  <svg class="team-arrow" style="left:58px" width="12" height="24" viewBox="0 0 12 24"><path d="M10 2L2 12l8 10" fill="none" stroke="#ccc" stroke-width="1.5"/></svg>
  <svg class="team-arrow" style="left:1130px" width="12" height="24" viewBox="0 0 12 24"><path d="M2 2l8 10-8 10" fill="none" stroke="#ccc" stroke-width="1.5"/></svg>

  <div class="member" style="left:100px">
    <div class="quote"><b style="left:22px;top:24px">“</b>Lorem Ipsum is simply dummy text of the printing and typesetting industry. Lorem Ipsum has been the industry's standard dummy text ever since...<b style="right:20px;bottom:14px">”</b></div>
    <h4>MARLO KESTRIN</h4><span>Marketing Executive</span>
  </div>
  <div class="member" style="left:358px">
    <div class="photo" role="img" aria-label="Portrait of a smiling businessman in a dark suit and red tie" style="background:radial-gradient(ellipse 70px 80px at 115px 85px,#c9a58e,rgba(201,165,142,0) 75%),linear-gradient(180deg,#f1f1f1 0%,#dedede 62%,#2c2c2e 72%,#1d1d20 100%)"></div>
    <h4>MARLO KESTRIN</h4><span>Marketing Executive</span>
  </div>
  <div class="member" style="left:617px">
    <div class="photo" role="img" aria-label="Portrait of a businessman in a blue suit talking on the phone" style="background:radial-gradient(ellipse 70px 80px at 115px 80px,#b58f78,rgba(181,143,120,0) 75%),linear-gradient(90deg,#7d848c,#a9afb5 60%,#5a6270),linear-gradient(180deg,transparent 60%,#4e6585 72%,#3d5270 100%)"></div>
    <h4>MARLO KESTRIN</h4><span>Marketing Executive</span>
  </div>
  <div class="member" style="left:874px">
    <div class="photo" role="img" aria-label="Portrait of a businesswoman in glasses and a blue blouse" style="background:radial-gradient(ellipse 75px 90px at 115px 85px,#6a4a3a,rgba(106,74,58,0) 75%),linear-gradient(180deg,#f4f4f4 0%,#e8e8e8 60%,#3f68b0 74%,#2f57a0 100%)"></div>
    <h4>MARLO KESTRIN</h4><span>Marketing Executive</span>
  </div>
</section>

<footer class="site-footer">
  <div class="footer-col" style="left:105px;width:300px">
    <h5>TESTIMONIALS <span style="position:absolute;left:263px;color:#888;font-weight:400">‹ ›</span></h5>
    <p class="testimonial"><b style="left:0;top:-6px">“</b>Simply dummy text of the printing and typesetting industry. Lorem Ipsum has been the industry's standard dummy text ever since the 1500s, when an unknown printer took a galley of type and scrambled it to make a type specimen book...<b style="right:-4px;bottom:-14px">”</b></p>
    <p class="testimonial-by"><b>MARLO KESTRIN</b> Marketing Executive</p>
  </div>
  <div class="footer-col" style="left:495px">
    <h5>WELCOME</h5>
    <ul><li>HOME</li><li>ABOUT US</li><li>SERVICES</li><li>CLIENTS</li><li>SOLUTIONS</li><li>CONTACT</li></ul>
  </div>
  <div class="footer-col" style="left:708px">
    <h5>INFORMATION</h5>
    <ul><li>PRIVACY POLICY</li><li>TERMS &amp; CONDITIONS</li><li>SITEMAP</li></ul>
  </div>
  <div class="footer-col" style="left:934px">
    <h5>FOLLOW US</h5>
    <ul class="social"><li><i></i>| PAGEWALL</li><li><i></i>| CHIRPLY</li><li><i></i>| TAGSTASH</li><li><i></i>| WANDERLY</li></ul>
  </div>
</footer>
<div class="footer-base">© 2015. VEL ENGINEERING SOLUTIONS. ALL RIGHTS RESERVED.</div>

</body>
</html>
```